BrimFalcon Business Cards

We have a defined brand. Please visit our website to get a feel for the product and the color pallets. www.brimfalcon-example.com

We need an updated, world class business card design. (See the attached existing card design). Please utilize BOTH sides of the card as shown and be creative with the layout. I do want the horse head icon to be positioned as it is with the existing card.

The remainder of the layout can be customized and I also want it vertically oriented.

Attached are the logo files and please use the colors as follows:
Green - #A5CE39
Tan - #CDBD99
Black

Feel free to play with the colors.

```html
<!DOCTYPE html>
<html lang="en">
<head>
<meta charset="utf-8">
<title>BrimFalcon Labs – Business Card</title>
<link rel="stylesheet" href="https://fonts.googleapis.com/css2?family=Exo+2:wght@600;700&family=Arimo:wght@400;700&display=swap">
<style>
  :root {
    --backdrop: #2b2b2d;
    --card: #1c1d1f;
    --white: #f4f4f4;
    --green: #a5ce39;
    --green-deep: #3fa535;
    --silver-hi: #f2f2f2;
    --silver-lo: #8d8d8d;
  }
  * { box-sizing: border-box; margin: 0; padding: 0; }
  html, body { width: 1200px; height: 1107px; overflow: hidden; }
  body {
    background: var(--backdrop);
    font-family: "Arimo", Arial, sans-serif;
    color: var(--white);
    position: relative;
  }
  .card {
    position: absolute;
    top: 190px;
    width: 440px;
    height: 720px;
    background: var(--card);
    border-radius: 22px;
    overflow: hidden;
    box-shadow: 0 18px 40px rgba(0,0,0,.55);
  }
  .card--front { left: 130px; }
  .card--back { left: 630px; }

  .brand { display: flex; align-items: center; gap: 12px; justify-content: center; }
  .brand__dot { width: 34px; height: 34px; border-radius: 50%; background: var(--white); flex: none; }
  .brand__name {
    font-family: "Exo 2", sans-serif;
    font-weight: 700;
    font-size: 36px;
    color: var(--white);
    letter-spacing: .5px;
    white-space: nowrap;
  }
  .tagline {
    font-weight: 700;
    font-size: 15px;
    letter-spacing: 5px;
    text-align: center;
    color: var(--white);
    margin-top: 6px;
    white-space: nowrap;
  }

  /* Front */
  .card--front .brand-block { position: absolute; top: 78px; left: 0; right: 0; }
  .person { position: absolute; top: 300px; left: 0; right: 0; text-align: center; }
  .person__name {
    font-family: "Exo 2", sans-serif;
    font-weight: 700;
    font-size: 29px;
    color: var(--green);
    letter-spacing: 1px;
    text-transform: uppercase;
  }
  .person__title { font-size: 19px; margin-top: 4px; }
  .icon-row {
    position: absolute; top: 392px; left: 70px; right: 70px;
    display: flex; align-items: center; gap: 10px;
  }
  .icon-row__rule { flex: 1; height: 1.5px; background: var(--white); }
  .icon {
    width: 36px; height: 36px; border-radius: 50%;
    border: 2px solid var(--white);
    display: flex; align-items: center; justify-content: center;
  }
  .icon__inner {
    width: 26px; height: 26px; border-radius: 50%;
    background: var(--green);
    display: flex; align-items: center; justify-content: center;
  }
  .contacts {
    position: absolute; top: 456px; left: 0; right: 0;
    text-align: center; font-size: 19px; line-height: 1.45;
  }
  .contacts .accent { color: var(--green); }
  .divider { position: absolute; top: 580px; left: 85px; right: 85px; height: 1.5px; background: var(--white); }
  .address {
    position: absolute; top: 604px; left: 0; right: 0;
    text-align: center; font-size: 19px; line-height: 1.3; font-style: normal;
  }

  /* Back */
  .emblem-area {
    position: absolute; top: 0; left: 0; right: 0; height: 540px;
    background: radial-gradient(ellipse at 55% 40%, var(--silver-hi) 0%, #bdbdbd 45%, var(--silver-lo) 75%, var(--card) 100%);
  }
  .card--back .brand-block { position: absolute; top: 548px; left: 0; right: 0; }
  .card--back .brand__name { font-size: 40px; }
  .band {
    position: absolute; left: 0; right: 0; top: 648px; height: 40px;
    background: linear-gradient(90deg, var(--green) 0%, var(--green) 45%, var(--green-deep) 100%);
    display: flex; align-items: center; justify-content: center;
    font-size: 20px; letter-spacing: 1px; color: #1a1a1a; text-transform: uppercase;
  }
</style>
</head>
<body>
  <section class="card card--front" aria-label="Business card front">
    <div class="brand-block">
      <div class="brand"><span class="brand__dot"></span><span class="brand__name">BrimFalcon Labs</span></div>
      <p class="tagline">Precision Tuned Motion</p>
    </div>

    <div class="person">
      <h1 class="person__name">Marcus Delane</h1>
      <p class="person__title">President &amp; CEO</p>
    </div>

    <div class="icon-row">
      <span class="icon-row__rule"></span>
      <span class="icon"><span class="icon__inner">
        <svg width="14" height="14" viewBox="0 0 24 24" aria-label="Phone"><path fill="#1c1d1f" d="M6.6 10.8a15 15 0 0 0 6.6 6.6l2.2-2.2c.3-.3.7-.4 1-.2 1.1.4 2.3.6 3.6.6.6 0 1 .4 1 1V20c0 .6-.4 1-1 1A17 17 0 0 1 3 4c0-.6.4-1 1-1h3.5c.6 0 1 .4 1 1 0 1.3.2 2.5.6 3.6.1.3 0 .7-.2 1z"/></svg>
      </span></span>
      <span class="icon"><span class="icon__inner">
        <svg width="15" height="12" viewBox="0 0 24 18" aria-label="Email"><rect x="1" y="1" width="22" height="16" rx="1.5" fill="#1c1d1f"/><path d="M2 2l10 8 10-8" fill="none" stroke="#a5ce39" stroke-width="2"/></svg>
      </span></span>
      <span class="icon"><span class="icon__inner">
        <svg width="15" height="15" viewBox="0 0 24 24" aria-label="Website"><circle cx="12" cy="12" r="10" fill="none" stroke="#1c1d1f" stroke-width="2"/><ellipse cx="12" cy="12" rx="4.5" ry="10" fill="none" stroke="#1c1d1f" stroke-width="2"/><path d="M2 12h20" stroke="#1c1d1f" stroke-width="2"/></svg>
      </span></span>
      <span class="icon-row__rule"></span>
    </div>

    <div class="contacts">
      <p>555.010.7384</p>
      <p>marcus@brimfalcon-example.com</p>
      <p>www.<span class="accent">brimfalcon-example</span>.com</p>
    </div>

    <div class="divider"></div>

    <address class="address">Brookhaven, Westland<br>Canada</address>
  </section>

  <section class="card card--back" aria-label="Business card back">
    <div class="emblem-area" role="img" aria-label="Large metallic silver brand emblem artwork"></div>
    <div class="brand-block">
      <div class="brand"><span class="brand__name">BrimFalcon Labs</span></div>
      <p class="tagline">Precision Tuned Motion</p>
    </div>
    <div class="band">Journeys Redesigned</div>
  </section>
</body>
</html>
```